NZ First of it's kind solutions directory and marketplace for busy Mums needs a business card design

We need a business card design for our new nationwide business in NZ (long term plans to go global). We provide solutions to the everyday challenges that busy Mums face by connecting them with quality communities and suppliers of carefully selected, relevant products and services. We sell direct via our online marketplace. The final design should communicate our values of inclusivity, quality and smart solutions. Colours should incorporate our logo colour palette of #477077 and #6ba8b2. Our website is at https://www.brightnestmums.example

Target Market(s)

busy Mums, Age 28 – 50, female, income over $100K, location main centres NZ primarily but NZ wide. Is likely juggling work or career with a young family. Probably had hobbies which have fallen by the wayside.
-Wants to succeed in her chosen career without compromising on family life
-to successfully juggle her career without feeling like she is compromising her children
- Is time poor, something always has to give and it’s generally her health (she’ll stay up late, get stressed)
- probably ex corporate or professional career. Has discretional income

Industry/Entity Type

Business

Contact Information for Business Card

Lena Forbisher, Founder, BrightNestMums.example (Strapline Tap; Gather; Sorted), 47 Kowhai Terrace, Ellerslie, Auckland 1051, New Zealand. Mob: 021 483 517 Ph: +64 (0)9 571 4860

Font styles to use
Other font styles liked:
• Raleway, and/or Architects Daughter

Colors
00a990
33b8a4
86cfc6
cfeae6

Requirements
Must have
• the above details, streamline. the logo and colours associated with those logos
Should not have
• foil or metallic colours

```html
<!DOCTYPE html>
<html lang="en">
<head>
<meta charset="utf-8">
<title>BrightNestMums – Business Card</title>
<link href="https://fonts.googleapis.com/css2?family=Raleway:wght@400;500;700;800&display=swap" rel="stylesheet">
<style>
  :root {
    --teal: #00a98f;
    --teal-text: #14a58e;
    --mint: #cfeae6;
    --slate: #477077;
    --steel: #6ba8b2;
    --white: #ffffff;
    --backdrop: #e9eceb;
  }
  * { margin: 0; padding: 0; box-sizing: border-box; }
  html, body {
    width: 1200px; height: 1000px; overflow: hidden;
    background: var(--backdrop);
    font-family: 'Raleway', sans-serif;
  }
  .canvas { position: relative; width: 1200px; height: 1000px; }

  .card {
    position: absolute;
    border-radius: 30px;
    overflow: hidden;
    box-shadow: 0 6px 14px rgba(0,0,0,0.18);
  }

  /* Front */
  .card-front {
    left: 150px; top: 103px; width: 628px; height: 358px;
    background: var(--teal);
  }
  .card-front .wave { position: absolute; left: 0; top: 0; }
  .brand {
    position: absolute;
    display: flex; align-items: center; gap: 12px;
    font-weight: 800; letter-spacing: -0.5px;
  }
  .brand-dot { border-radius: 50%; flex: none; }
  .card-front .brand { left: 160px; top: 138px; font-size: 38px; color: var(--white); }
  .card-front .brand-dot { width: 30px; height: 30px; background: var(--mint); }

  /* Back */
  .card-back {
    left: 371px; top: 547px; width: 635px; height: 362px;
    background: var(--white);
  }
  .card-back .brand { left: 30px; top: 40px; font-size: 28px; color: var(--slate); gap: 10px; }
  .card-back .brand-dot { width: 26px; height: 26px; background: var(--steel); }

  .holder {
    position: absolute; left: 0; width: 100%; top: 104px;
    text-align: center; color: var(--teal-text);
  }
  .holder-name { font-size: 30px; font-weight: 400; line-height: 36px; }
  .holder-role { font-size: 19px; font-weight: 400; line-height: 24px; }

  .rule {
    position: absolute; left: 0; top: 171px; width: 100%;
    height: 2px; background: var(--teal);
  }
  .address-band {
    position: absolute; left: 62px; top: 173px; width: 512px; height: 26px;
    background: var(--teal);
    border-radius: 0 0 14px 14px;
    color: var(--white); font-size: 17px; font-weight: 500;
    display: flex; align-items: center; justify-content: center;
  }

  .contacts { position: absolute; left: 44px; top: 220px; list-style: none; }
  .contact {
    display: flex; align-items: center; gap: 14px;
    height: 35px; color: var(--teal-text); font-size: 19px;
  }
  .contact svg { width: 24px; height: 24px; flex: none; }
  .strapline { font-size: 14px; margin-left: 4px; }
</style>
</head>
<body>
<div class="canvas">

  <section class="card card-front" aria-label="Card front">
    <svg class="wave" width="628" height="358" viewBox="0 0 628 358" aria-hidden="true">
      <path d="M0 234 C120 204, 220 324, 330 323 C440 322, 520 228, 628 234" fill="none" stroke="#ffffff" stroke-width="3"/>
    </svg>
    <div class="brand"><span class="brand-dot"></span>BrightNestMums</div>
  </section>

  <section class="card card-back" aria-label="Card back">
    <div class="brand"><span class="brand-dot"></span>BrightNestMums</div>

    <div class="holder">
      <p class="holder-name">Lena Forbisher</p>
      <p class="holder-role">Founder</p>
    </div>

    <div class="rule"></div>
    <div class="address-band">47 Kowhai Terrace, Ellerslie, Auckland 1051, New Zealand</div>

    <ul class="contacts">
      <li class="contact">
        <svg viewBox="0 0 24 24" aria-label="Phone"><path fill="#00a98f" d="M3 8c0-3 4-4 9-4s9 1 9 4v2h-5V8H8v2H3z M6 11h12l2 8H4z"/><circle cx="12" cy="15" r="2.5" fill="#fff"/></svg>
        <span>+64 (0)9 571 4860</span>
      </li>
      <li class="contact">
        <svg viewBox="0 0 24 24" aria-label="Mobile"><path fill="#00a98f" d="M6.6 10.8a15 15 0 0 0 6.6 6.6l2.2-2.2c.3-.3.7-.4 1-.2 1.1.4 2.3.6 3.6.6.6 0 1 .4 1 1V20c0 .6-.4 1-1 1A17 17 0 0 1 3 4c0-.6.4-1 1-1h3.5c.6 0 1 .4 1 1 0 1.3.2 2.5.6 3.6.1.3 0 .7-.2 1z"/></svg>
        <span>021 483 517</span>
      </li>
      <li class="contact">
        <svg viewBox="0 0 24 24" aria-label="Website"><g fill="none" stroke="#00a98f" stroke-width="2"><circle cx="12" cy="12" r="9"/><ellipse cx="12" cy="12" rx="4" ry="9"/><path d="M3 12h18M5 7h14M5 17h14"/></g></svg>
        <span>www.brightnestmums.example<span class="strapline">( Strapline Tap; Gather; Sorted )</span></span>
      </li>
    </ul>
  </section>

</div>
</body>
</html>
```